Heron Property Inspection business card

I am the principal inspector of Heron Property Inspections. I serve Northern Virginia from Winchester to Arlington.Associate, Federated Guild of Dwelling Examiners (FGDE)Graduate, FGDE Home Inspectors CourseNational Association of Home Inspectors ExamI'd like the business card to look more professional than comical.I pulled the attached picture off the web. I'd like to have something like that or an image of a house as my logo on the cards.

Target Market(s)

Persons who recently purchased a home.

Industry/Entity Type

Business

Contact Information for Business Card

Bob AllenBadger Home Inspections, LLC.4455 River RoadBluemont, Virginia 20135cell: 703-231-6680e-mail: tkmarlow@postvale.net

Font styles to use
Serif
Sans Serif

Requirements
Must have
• I'd like to have a logo, something that identifies me as a home inspector. The attached images are something that I'd like to have incorporated into my business card logo.
Nice to have
• I'd like a sketch of a house and/or a magnifying glass showing a house being inspected. The attached images are used as a suggestion only, I do not own the images.
Should not have
• Gimmicky stuff. I want to appear professional and trustworthy.

```html
<!DOCTYPE html>
<html lang="en">
<head>
<meta charset="utf-8">
<title>Heron Property Inspections – Business Card</title>
<link rel="stylesheet" href="https://fonts.googleapis.com/css2?family=Marcellus&family=Arimo:wght@400&display=swap">
<style>
  :root {
    --canvas: #e9e6e1;
    --card: #fbfbfa;
    --brand-red: #b3202a;
    --band-red: #b8262e;
    --ink: #3a3a3c;
    --on-red: #ffffff;
  }
  * { box-sizing: border-box; margin: 0; padding: 0; }
  html, body {
    width: 1200px; height: 892px; overflow: hidden;
    background: var(--canvas);
  }
  .business-card {
    position: absolute; left: 100px; top: 160px;
    width: 1000px; height: 571px;
    background: var(--card);
    box-shadow: 0 6px 24px rgba(0,0,0,0.18);
  }
  .card-frame {
    position: absolute; inset: 22px;
    border: 2px solid var(--brand-red);
  }
  .brand-lockup {
    position: absolute; left: 340px; top: 92px;
    display: flex; align-items: center; gap: 16px;
    font-family: "Marcellus", serif;
    color: var(--ink);
  }
  .brand-mark {
    width: 22px; height: 22px; background: var(--brand-red);
  }
  .brand-name { font-size: 34px; line-height: 1.2; }
  .person {
    position: absolute; left: 0; right: 0; top: 238px;
    text-align: center; font-family: "Arimo", sans-serif;
  }
  .person-name { font-size: 40px; color: var(--brand-red); line-height: 1.1; padding-left: 40px; }
  .person-role { font-size: 22px; color: var(--ink); margin-top: 2px; padding-left: 40px; }
  .contact-band {
    position: absolute; left: 22px; right: 22px; top: 440px; height: 92px;
    background: var(--band-red);
    display: flex; align-items: center;
    font-family: "Arimo", sans-serif; color: var(--on-red); font-size: 24px;
  }
  .contact-item { padding: 0 30px; }
  .contact-divider { width: 2px; height: 46px; background: var(--on-red); opacity: 0.9; }
  .contact-email { width: 400px; text-align: center; }
  .contact-phone { width: 230px; text-align: center; }
  .contact-address { flex: 1; text-align: right; line-height: 1.1; }
</style>
</head>
<body>
  <div class="business-card">
    <div class="card-frame"></div>

    <div class="brand-lockup">
      <span class="brand-mark"></span>
      <div class="brand-name">Tim Marlow<br>Heron Property Inspections, LLC</div>
    </div>

    <div class="person">
      <div class="person-name">Employee Name</div>
      <div class="person-role">Your Position</div>
    </div>

    <div class="contact-band">
      <div class="contact-item contact-email">tkmarlow@postvale.net</div>
      <span class="contact-divider"></span>
      <div class="contact-item contact-phone">703-555-0192</div>
      <span class="contact-divider"></span>
      <div class="contact-item contact-address">7182 Quarry Lane, Fernhill,<br>Virginia 20148</div>
    </div>
  </div>
</body>
</html>
```